Printed Circuit Board Company Web Site Design - Please see new file 82012 web design

We are a printed circuit board manufacturer. Need a company professional web site to allow our potential customers to know more about our background, capability and our products. The web site will contain three languages, which are Chinese, English and Japanese. Our audience are mainly electronic companies that procure printed circuit boards. I have a word document that have all the required text in all three languages. The final design should communicate the impression that we embrace quality, trustworthiness and long term partnership business principles.
We should have sections that allow us to post pictures of our facilities.
I have added the three files in three different languages.
Some of the information is below:
Background
RDV Harbourline Limited (RDV) was set up in Hong Kong in 2007 by two Hong Kong entrepreneurs, Mr. Tak Wong and Mr. Lok Fai. We acquired the single sided printed circuit board factory located in Dongguan City, Guangdong Province, China, from Tovand Corporation of the U.S. in 2007. In addition to RDV, Mr. Wong and Mr. Fai also own Halberd Technology Company Limited, a semiconductor company based in Hong Kong since 1997 with a total investment of over US$100 million. Halberd is engaged in the manufacturing of flexible substrates and MEMS assembly business.
RDV has been awarded TS 16949 and ISO14000 certificates since 2009 and 2004 respectively.
Business Principles
RDV Harbourline Limited strives to be a professional top notched printed circuit board supplier. We embrace four “EXCELLENCE” principles, namely, excellence in quality, excellence in prices, excellence in services and excellence in on time delivery.
We approach each customer with a long-term partnership view that delivers the lowest ownership costs and highest total values to our customers. We customize quotations and solutions in order to allow our customers to win more businesses. We believe by thinking from our customers’ points of view we will be able to create a WIN-WIN relationship.
Customers
Due to our excellent quality, services and production systems, RDV Harbourline Limited manage to service a number of large Japanese and US customers, which include:
Technical capability overview
Below is an overview of our current capability:
Target Market(s)
Electronic companies buyers
Industry/Entity Type
Business
Requirements
Must have
- Capability description
Should not have
- no cartoon

```html
<!DOCTYPE html>
<html lang="en">
<head>
<meta charset="utf-8">
<title>RDV Harbourline Limited – Products</title>
<link href="https://fonts.googleapis.com/css2?family=Arimo:wght@400;700&family=Cinzel:wght@400&family=Oswald:wght@300;400&family=Alfa+Slab+One&display=swap" rel="stylesheet">
<style>
:root{
  --teal:#0b7a62;
  --teal-dark:#06614d;
  --orange:#f7941d;
  --orange-light:#fbab45;
  --text:#4a4a4a;
  --line:#c9c9c9;
  --field:#f4f4f4;
  --white:#ffffff;
}
*{margin:0;padding:0;box-sizing:border-box}
html,body{width:1200px;height:920px;overflow:hidden;background:var(--white)}
body{position:relative;font-family:"Arimo",Arial,sans-serif;color:var(--text)}
.abs{position:absolute}
.top-band{left:0;top:0;width:1200px;height:7px;background:var(--teal)}
.header{left:0;top:7px;width:1200px;height:78px;background:#f7f9f8}
.brand{left:180px;top:18px;display:flex;align-items:center;gap:8px;font:700 30px "Arimo",Arial,sans-serif;color:var(--teal)}
.brand-mark{width:14px;height:14px;background:var(--teal)}
.brand small{font-size:14px;font-weight:700;line-height:1.1;display:block}
.phone{right:181px;top:24px;display:flex;align-items:center;gap:8px;font-size:19px;color:#111}
.nav{left:0;top:85px;width:1200px;height:34px;background:linear-gradient(var(--teal),var(--teal-dark))}
.nav-link{position:absolute;top:0;height:34px;font:400 13.5px "Cinzel",serif;line-height:34px;text-align:center;color:var(--white);letter-spacing:1px;text-decoration:none;border-right:1px solid rgba(255,255,255,.18)}
.nav-link.active{background:linear-gradient(var(--orange-light),var(--orange))}
.login{left:956px;top:69px;width:62px;height:50px;border-radius:5px 5px 0 0;background:linear-gradient(var(--orange-light),var(--orange));color:var(--white);font:700 12px "Arimo",sans-serif;text-align:center;padding-top:6px}
.banner{left:0;top:119px;width:1200px;height:161px;border:1px solid #8fc7b8;background:linear-gradient(90deg,#eef5f8 0%,#e6f0f4 50%,#f1f5f6 100%)}
.hero-photo{left:640px;top:120px;width:559px;height:159px;background:linear-gradient(90deg,rgba(230,238,241,0) 0%,#c9d2d4 25%,#8e9698 45%,#d9c2ae 68%,#b89a7c 78%,#e9eef0 100%)}
.banner-title{left:178px;top:165px;font:400 48px "Cinzel",serif;color:var(--teal)}
.product{left:152px;width:560px}
.product-title{font:300 27px "Oswald",sans-serif;color:var(--orange);display:flex;align-items:center;gap:12px}
.product-title::before{content:"";width:12px;height:12px;border:2px solid var(--orange);background:linear-gradient(135deg,var(--white) 50%,var(--orange) 50%)}
.product-text{margin:8px 0 0 26px;width:532px;font-size:13.8px;line-height:20.5px;text-align:justify}
.quick{left:751px;top:321px;width:278px;height:292px;border:2px solid #e0e0e0;border-radius:14px;background:#ededed}
.quick-title{left:784px;top:321px;width:210px;height:52px;background:linear-gradient(var(--orange-light),var(--orange));color:var(--white);font:400 19px "Alfa Slab One",serif;line-height:52px;letter-spacing:1px;text-align:center}
.field{left:780px;width:222px;height:30px;background:var(--field);border:1px solid #d2d2d2;font-size:12.5px;color:#777;padding:8px 11px;letter-spacing:.5px}
.submit{left:934px;top:578px;width:68px;height:26px;background:var(--orange);color:var(--white);font:700 10.5px "Arimo",sans-serif;line-height:26px;letter-spacing:1.5px;text-align:center}
.customers{left:178px;top:645px;width:849px;height:94px;border:1px solid var(--line)}
.customers-title{left:190px;top:624px;padding:0 9px;background:var(--white);font:400 24px "Oswald",sans-serif;color:var(--orange)}
.client{top:670px;height:44px;display:flex;align-items:center;justify-content:center;font:700 19px "Arimo",sans-serif}
.arrow{top:678px}
.footer{left:0;top:764px;width:1200px;height:124px;background:linear-gradient(var(--teal),#0a7060)}
.footer-heading{left:178px;top:773px;font:700 11px "Arimo",sans-serif;color:var(--white)}
.links{top:800px;list-style:none;font-size:9.5px;line-height:15.5px;color:var(--white)}
.links li::before{content:"▸ ";font-size:7px}
.address{right:177px;top:776px;text-align:right;font-style:normal;font-size:9.5px;line-height:15.5px;color:var(--white)}
.address strong{font-size:11px}
.copyright{left:0;top:888px;width:1200px;height:32px;background:var(--teal-dark);color:var(--white);font:700 9.5px "Arimo",sans-serif;line-height:30px;text-align:center}
</style>
</head>
<body>
<div class="abs top-band"></div>
<header class="abs header"></header>
<div class="abs brand"><span class="brand-mark"></span><span>RDV<small>Harbourline Limited</small></span></div>
<div class="abs phone">
  <svg width="24" height="20" viewBox="0 0 24 20"><path d="M3 4c0-2 3-3 5-2l2 3-2 3c1 3 4 6 7 7l3-2 3 2c1 2 0 5-2 5C10 20 3 12 3 4z" fill="#0b7a62"/></svg>
  (852) 2046 5318
</div>
<nav class="abs nav">
  <a class="nav-link" style="left:150px;width:107px">HOME</a>
  <a class="nav-link active" style="left:257px;width:138px">PRODUCTS</a>
  <a class="nav-link" style="left:395px;width:127px">SERVICES</a>
  <a class="nav-link" style="left:522px;width:239px">TECHNICAL CAPABILITIES</a>
  <a class="nav-link" style="left:761px;width:142px">CONTACT US</a>
</nav>
<div class="abs login">
  <svg width="14" height="18" viewBox="0 0 14 18"><path d="M3 8V5a4 4 0 0 1 8 0v3" stroke="#fff" stroke-width="2" fill="none"/><rect x="1" y="8" width="12" height="9" rx="1" fill="#fff"/></svg><br>LOGIN
</div>
<div class="abs banner"></div>
<div class="abs hero-photo" role="img" aria-label="Photo of a smiling businesswoman with colleagues working in a bright office"></div>
<h1 class="abs banner-title">PRODUCTS</h1>

<section class="abs product" style="top:320px">
  <h2 class="product-title">Single Layered Printed Circuit Boards</h2>
  <p class="product-text">We currently are offering single layered circuit boards through our own production facility in China for customers in the audio and video industry, home appliance and camera, industrial equipment and power supply, automotive, as well as contract manufacturers.</p>
</section>
<section class="abs product" style="top:462px">
  <h2 class="product-title">Double Layered And Multi-Layered Printed Circuit Boards</h2>
  <p class="product-text">We are offering two layered and multi-layered circuit boards for our customers through our strategically approved printed circuit boards manufacturers.</p>
</section>

<div class="abs quick"></div>
<div class="abs quick-title">QUICK CONTACT</div>
<div class="abs field" style="top:381px">Name:</div>
<div class="abs field" style="top:415px">Email:</div>
<div class="abs field" style="top:449px">Company Name:</div>
<div class="abs field" style="top:484px;height:87px">Comments:</div>
<div class="abs submit">SUBMIT</div>

<div class="abs customers"></div>
<h3 class="abs customers-title">OUR CUSTOMERS</h3>
<svg class="abs arrow" style="left:155px" width="18" height="22" viewBox="0 0 18 22"><path d="M14 2 L4 11 L14 20" stroke="#bbb" stroke-width="4" fill="none"/></svg>
<svg class="abs arrow" style="left:1031px" width="18" height="22" viewBox="0 0 18 22"><path d="M4 2 L14 11 L4 20" stroke="#bbb" stroke-width="4" fill="none"/></svg>
<div class="abs client" style="left:200px;width:110px;color:#e57f2b;font-weight:400">Corvane</div>
<div class="abs client" style="left:340px;width:120px;color:#1d3f7c;font-size:13px">Aldermoor Power</div>
<div class="abs client" style="left:498px;width:190px;color:#1f5f9c">Voltrisa</div>
<div class="abs client" style="left:722px;width:103px;background:#102e6a;color:#fff">KORU</div>
<div class="abs client" style="left:850px;width:145px;color:#1a2a2a;font-size:26px">TAKEMI</div>

<footer class="abs footer"></footer>
<h4 class="abs footer-heading">POPULAR LINKS</h4>
<ul class="abs links" style="left:178px">
  <li>Sitemap</li><li>Circuit Boards</li><li>Capabilities</li><li>Industries Served</li><li>About Us</li>
</ul>
<ul class="abs links" style="left:320px">
  <li>Contact Us</li><li>Resources</li><li>Service Center</li><li>News &amp; Events</li><li>Privacy Policy</li>
</ul>
<address class="abs address">
  <strong>RDV Harbourline Limited</strong><br>
  28/F Marlow Tower<br>
  12 Kestrel Road<br>
  Wan Chai, HONG KONG<br>
  Telephone: (852)20465318<br>
  Fax: (852)20465319<br>
  Email: sales@rdvboard.example
</address>
<div class="abs copyright">COPYRIGHT © 2012 RDV HARBOURLINE LIMITED. ALL RIGHTS RESERVED</div>
</body>
</html>
```